UI/UX Re-Do for TallyNest - a free to use project management platform for desktop and mobile.

UI/UX Re-Do for TallyNest
TallyNest is a free to use project management platform for desktop and mobile.
We are looking for help with our UI/UX re-design.
As of now the platform is totally functional.
The problem is around flow and look. We want TN to become something that any one can use to manage and even socialize any project. A project can be something work related like organizing a team around a software build, marketing campaign, shared client file space, etc... In fact, most of our current members are using TN for just such work projects.
We also see a project as planning a wedding, organizing a group trip, a simple to-do list, organizing a kids sports team, and so on...
To become a platform that people will use in their work and personal life we first need to become more intuitive and friendly - while maintaining advanced functionality for more advanced needs.
We need help to beautify, streamline, and simplify - while keeping all the functions.
The quickest way to understand TN, and our current issues is this short video:
https://vidlumo.example/w/Qa7KdP2mXzR
For sure see this link for the entire most recent description AND images:
https://tallynestapp.example/?p=HumbZ4KcWrT
The best way to understand TN is to actually use it:
https://tallynestapp.example
Should you choose to take a run at improving TN here are the details:
Please focus your ideas for mobile, it's where we have the biggest issues.
Feel free to get outside the box.
Avoid swipe oriented designs.
Feel free to focus on ideas over polished outputs.
Use any tool you like, PS, hand drawing, written description if you think that works best.
(FYI - we use mostly use Orvane Slides docs internally)
Point is illustration of ideas over tool choice.
Feel free to:
Create something totally new
And/or riff on what we have now
And/or riff on the new design we are considering (see images below)
|||
If we go the direction of the images/designs below the idea is to give people options on how they see/experience TN.
Just below is what we are calling Ground View. This is a more basic and simple flow. Probably a default to keep new users feeling comfortable at the start.
<img src="https://i.picbarn.example/8wNtLQe.jpg" style="width: 100%;">
https://i.picbarn.example/8wNtLQe.jpg
|||
We are calling this optional view Sky View. It is more advanced and can show all project, goal(renamed 'milestones') at the same time. This is more of a paint job on the current design.
<img src="https://i.picbarn.example/vhRmJxd.jpg" style="width: 100%;">
https://i.picbarn.example/vhRmJxd.jpg
|||
If you're submitting please let us know if you can also do the PS files for dev.
Not required, but once we nail down the concepts we want someone to hone in the PS files.
As an optional bonus we will also be giving credit to you/your company in TN.
Let us know if you do or don't want that.
We are excited to see your work!!
<img src=" " style="width: 100%;">
Target Market(s)
Anyone who needs to organize any project, big or small. The key is to make a super friendly user experience for new users while retaining advanced functions.
Industry/Entity Type
Management
Number of Pages Required
2 page

```html
<!DOCTYPE html>
<html lang="en">
<head>
<meta charset="utf-8">
<title>TallyNest – Milestones Calendar</title>
<link rel="stylesheet" href="https://fonts.googleapis.com/css2?family=Montserrat:wght@400;500;600;700&family=Ubuntu:wght@400;500&display=swap">
<style>
  :root {
    --sky-top: #08a3e3;
    --sky: #03aeef;
    --white: #ffffff;
    --ink: #1d1d1d;
    --muted: #8a8a8a;
    --label: #a3a3a3;
    --rule: #d6d6d6;
    --link: #1a8fe8;
    --today: #ee3d6b;
    --action: #ee1c25;
    --cal-red: #e8453c;
    --cal-grey: #c9cfd4;
  }
  * { box-sizing: border-box; margin: 0; padding: 0; }
  html, body { width: 675px; height: 1200px; overflow: hidden; background: var(--white); }
  .screen { position: relative; width: 675px; height: 1200px; overflow: hidden; font-family: "Montserrat", sans-serif; background: var(--white); }

  .calendar { position: absolute; left: 0; top: 0; width: 675px; height: 670px; background: linear-gradient(180deg, var(--sky-top) 0%, var(--sky) 110px, var(--sky) 100%); color: var(--white); border-bottom: 1px solid #cfd8dc; }
  .month-title { position: absolute; top: 30px; left: 0; width: 100%; text-align: center; font-size: 30px; font-weight: 600; letter-spacing: 0.5px; }
  .nav-btn { position: absolute; top: 26px; width: 42px; height: 42px; }
  .nav-btn.prev { left: 104px; }
  .nav-btn.next { left: 529px; }

  .weekday, .date { position: absolute; width: 60px; margin-left: -30px; text-align: center; }
  .weekday { top: 166px; font-size: 26px; font-weight: 700; }
  .date { font-family: "Ubuntu", sans-serif; font-size: 27px; letter-spacing: 1.5px; line-height: 32px; margin-top: -16px; }
  .today-mark { position: absolute; left: 292px; top: 493px; width: 62px; height: 62px; border-radius: 50%; background: var(--today); }

  .milestones { position: absolute; left: 0; top: 670px; width: 675px; height: 530px; border-right: 1px solid var(--rule); }
  .section-label { position: absolute; left: 90px; top: 17px; font-size: 11.5px; font-weight: 700; color: var(--label); letter-spacing: 0.5px; }
  .timeline-line { position: absolute; left: 89px; top: 78px; width: 1px; height: 460px; background: var(--rule); }
  .entry { position: absolute; left: 0; width: 675px; }
  .entry-dot { position: absolute; left: 80px; top: 1px; width: 19px; height: 19px; border-radius: 50%; border: 1.5px solid #c8c8c8; background: var(--white); }
  .entry-text { position: absolute; left: 131px; top: 0; width: 330px; font-size: 17px; line-height: 21px; color: var(--ink); }
  .entry-text .quiet { color: var(--muted); }
  .entry-text .file { color: var(--link); }
  .entry-time { position: absolute; left: 505px; width: 56px; text-align: right; font-size: 17px; color: var(--muted); }

  .fab { position: absolute; border-radius: 50%; display: flex; align-items: center; justify-content: center; }
  .fab-calendar { left: 552px; top: 959px; width: 84px; height: 84px; background: var(--white); box-shadow: 0 3px 10px rgba(0,0,0,0.18); }
  .fab-add { left: 540px; top: 1058px; width: 108px; height: 108px; background: var(--action); box-shadow: 0 4px 12px rgba(0,0,0,0.2); }
</style>
</head>
<body>
<main class="screen">
  <section class="calendar" aria-label="April 2013 calendar">
    <svg class="nav-btn prev" viewBox="0 0 42 42" aria-label="Previous month"><circle cx="21" cy="21" r="19" fill="none" stroke="#fff" stroke-width="3"/><path d="M24 13 L16 21 L24 29" fill="none" stroke="#fff" stroke-width="3" stroke-linecap="round" stroke-linejoin="round"/></svg>
    <h1 class="month-title">APRIL 2013</h1>
    <svg class="nav-btn next" viewBox="0 0 42 42" aria-label="Next month"><circle cx="21" cy="21" r="19" fill="none" stroke="#fff" stroke-width="3"/><path d="M18 13 L26 21 L18 29" fill="none" stroke="#fff" stroke-width="3" stroke-linecap="round" stroke-linejoin="round"/></svg>

    <span class="weekday" style="left:51px">S</span>
    <span class="weekday" style="left:145px">M</span>
    <span class="weekday" style="left:230px">T</span>
    <span class="weekday" style="left:325px">W</span>
    <span class="weekday" style="left:421px">R</span>
    <span class="weekday" style="left:523px">F</span>
    <span class="weekday" style="left:613px">S</span>

    <span class="today-mark"></span>

    <span class="date" style="left:615px;top:243px">1</span>

    <span class="date" style="left:51px;top:313px">2</span>
    <span class="date" style="left:141px;top:313px">3</span>
    <span class="date" style="left:231px;top:313px">4</span>
    <span class="date" style="left:331px;top:313px">5</span>
    <span class="date" style="left:430px;top:313px">6</span>
    <span class="date" style="left:530px;top:313px">7</span>
    <span class="date" style="left:619px;top:313px">8</span>

    <span class="date" style="left:51px;top:383px">9</span>
    <span class="date" style="left:141px;top:383px">10</span>
    <span class="date" style="left:227px;top:383px">11</span>
    <span class="date" style="left:323px;top:383px">12</span>
    <span class="date" style="left:421px;top:383px">13</span>
    <span class="date" style="left:518px;top:383px">14</span>
    <span class="date" style="left:604px;top:383px">15</span>

    <span class="date" style="left:52px;top:454px">16</span>
    <span class="date" style="left:141px;top:454px">17</span>
    <span class="date" style="left:223px;top:454px">18</span>
    <span class="date" style="left:319px;top:454px">19</span>
    <span class="date" style="left:418px;top:454px">20</span>
    <span class="date" style="left:516px;top:454px">21</span>
    <span class="date" style="left:603px;top:454px">22</span>

    <span class="date" style="left:52px;top:524px">23</span>
    <span class="date" style="left:141px;top:524px">24</span>
    <span class="date" style="left:228px;top:524px">25</span>
    <span class="date" style="left:323px;top:524px">26</span>
    <span class="date" style="left:420px;top:524px">27</span>
    <span class="date" style="left:517px;top:524px">28</span>
    <span class="date" style="left:603px;top:524px">29</span>

    <span class="date" style="left:52px;top:594px">30</span>
  </section>

  <section class="milestones">
    <h2 class="section-label">MILESTONES</h2>
    <span class="timeline-line"></span>

    <div class="entry" style="top:68px">
      <span class="entry-dot"></span>
      <p class="entry-text">Project setup</p>
      <span class="entry-time" style="top:-6px">10s</span>
    </div>
    <div class="entry" style="top:140px">
      <span class="entry-dot"></span>
      <p class="entry-text">Task assignment</p>
      <span class="entry-time" style="top:2px">3m</span>
    </div>
    <div class="entry" style="top:212px">
      <span class="entry-dot" style="top:0"></span>
      <p class="entry-text" style="top:-13px">Theo Marsh <span class="quiet">attached a file to task</span><br><span class="file">user guide.pdf</span></p>
      <span class="entry-time" style="top:-8px">5m</span>
    </div>
    <div class="entry" style="top:288px">
      <span class="entry-dot" style="top:0"></span>
      <p class="entry-text" style="top:-14px">Theo Marsh <span class="quiet">added</span> Lena Marsh <span class="quiet">to project</span></p>
      <span class="entry-time" style="top:-5px">10m</span>
    </div>
    <div class="entry" style="top:360px">
      <span class="entry-dot"></span>
      <p class="entry-text" style="width:360px">Theo Marsh <span class="quiet">added</span> a response to task</p>
      <span class="entry-time" style="top:0;left:495px;width:59px">2h</span>
    </div>
  </section>

  <div class="fab fab-calendar" aria-label="Calendar view">
    <svg width="40" height="40" viewBox="0 0 40 40" aria-hidden="true">
      <rect x="3" y="7" width="34" height="30" rx="3" fill="#e4e8eb"/>
      <rect x="3" y="7" width="34" height="9" rx="3" fill="var(--cal-red)"/>
      <rect x="3" y="12" width="34" height="4" fill="var(--cal-red)"/>
      <rect x="11" y="3" width="3" height="8" rx="1.5" fill="#7b8389"/>
      <rect x="26" y="3" width="3" height="8" rx="1.5" fill="#7b8389"/>
      <g fill="#9aa3aa">
        <rect x="8" y="19" width="4" height="3"/><rect x="14" y="19" width="4" height="3"/><rect x="20" y="19" width="4" height="3"/><rect x="26" y="19" width="4" height="3"/><rect x="32" y="19" width="2" height="3"/>
        <rect x="8" y="24" width="4" height="3"/><rect x="14" y="24" width="4" height="3"/><rect x="20" y="24" width="4" height="3"/><rect x="26" y="24" width="4" height="3"/><rect x="32" y="24" width="2" height="3"/>
        <rect x="8" y="29" width="4" height="3"/><rect x="14" y="29" width="4" height="3"/><rect x="20" y="29" width="4" height="3"/><rect x="26" y="29" width="4" height="3"/>
      </g>
    </svg>
  </div>
  <div class="fab fab-add" aria-label="Add milestone">
    <svg width="30" height="30" viewBox="0 0 30 30" aria-hidden="true"><path d="M15 2 V28 M2 15 H28" stroke="#fff" stroke-width="3.2" stroke-linecap="round"/></svg>
  </div>
</main>
</body>
</html>
```